Road Construction Company needs business cards

We would like a new business card designed for our business.

We're a road construction company based in Qld, Australia.

Can the business card please have the following information on it.

Name: Warren Halbeck
Position: General Manager
Phone: 0472 915 348
Email: Warren.halbeck@tovrin.com.au
Address: 87 Marrow Ave, Pendlebay, QLD, 4023
Website: www.tovrin.com.au

Visually we'd like the card to be professional and simple.

Attached is our logo.

Our website is www.tovrin.com.au

Target Market(s)

Men aged 25-60

Contact Information for Business Card

As listed in project description

Font styles to use
Serif

Requirements
Must have
• Large logo on back of card

```html
<!DOCTYPE html>
<html lang="en">
<head>
<meta charset="utf-8">
<title>Tovrin Road Construction – Business Card</title>
<link rel="stylesheet" href="https://fonts.googleapis.com/css2?family=Open+Sans:wght@400;600;700&display=swap">
<style>
  :root {
    --backdrop: #2b2b2e;
    --card: #000000;
    --edge: #3ea5e0;
    --brand-blue: #1a5db3;
    --accent-blue: #45a9e2;
    --shape-grey: #1e1e1f;
    --text-light: #ffffff;
  }
  * { box-sizing: border-box; margin: 0; padding: 0; }
  html, body {
    width: 1200px;
    height: 780px;
    overflow: hidden;
    background: var(--backdrop);
    font-family: "Open Sans", Arial, sans-serif;
  }
  .canvas {
    position: relative;
    width: 1200px;
    height: 780px;
  }
  .card {
    position: absolute;
    width: 630px;
    height: 360px;
    background: var(--card);
    border: 2px solid var(--edge);
    border-bottom-width: 5px;
    border-left-width: 4px;
    border-radius: 26px;
    overflow: hidden;
  }
  .card--back { left: 285px; top: 22px; }
  .card--front { left: 285px; top: 398px; }

  /* back */
  .brand-large {
    position: absolute;
    inset: 0;
    display: flex;
    align-items: center;
    justify-content: center;
    gap: 18px;
    color: var(--brand-blue);
    font-weight: 700;
    font-size: 96px;
    letter-spacing: 2px;
    text-transform: uppercase;
  }
  .brand-large .brand-mark {
    width: 34px;
    height: 34px;
    background: var(--brand-blue);
  }

  /* front */
  .accent-shape {
    position: absolute;
    left: 0; top: 0;
  }
  .holder {
    position: absolute;
    right: 38px;
    top: 62px;
    text-align: right;
  }
  .holder__name {
    color: var(--brand-blue);
    font-weight: 600;
    font-size: 27px;
    line-height: 1.1;
    text-transform: uppercase;
  }
  .holder__role {
    color: var(--text-light);
    font-size: 16px;
    font-weight: 600;
    margin-top: 2px;
  }
  .holder-bar {
    position: absolute;
    right: 18px;
    top: 58px;
    width: 14px;
    height: 50px;
    background: var(--accent-blue);
  }
  .brand-small {
    position: absolute;
    left: 40px;
    top: 128px;
    display: flex;
    align-items: center;
    gap: 10px;
    color: var(--brand-blue);
    font-weight: 700;
    font-size: 48px;
    text-transform: uppercase;
    letter-spacing: 1px;
  }
  .brand-small .brand-mark {
    width: 16px;
    height: 16px;
    background: var(--brand-blue);
  }
  .address {
    position: absolute;
    left: 40px;
    top: 208px;
    color: var(--text-light);
    font-size: 16px;
    line-height: 1.35;
  }
  .contacts {
    position: absolute;
    left: 40px;
    top: 262px;
    list-style: none;
    color: var(--text-light);
    font-size: 16px;
  }
  .contacts li {
    display: flex;
    align-items: center;
    gap: 10px;
    height: 24px;
  }
  .contacts svg { width: 15px; height: 15px; flex: none; }
</style>
</head>
<body>
<main class="canvas">

  <section class="card card--back" aria-label="Card back">
    <div class="brand-large"><span class="brand-mark"></span>Tovrin</div>
  </section>

  <section class="card card--front" aria-label="Card front">
    <svg class="accent-shape" width="630" height="360" viewBox="0 0 630 360" aria-hidden="true">
      <polygon points="420,38 630,100 630,122 530,138 552,360 520,360" fill="var(--shape-grey)"/>
    </svg>

    <div class="holder-bar"></div>
    <div class="holder">
      <p class="holder__name">Warren Halbeck</p>
      <p class="holder__role">General Manager</p>
    </div>

    <div class="brand-small"><span class="brand-mark"></span>Tovrin</div>

    <p class="address">87 Marrow Ave,<br>Pendlebay, QLD, 4023</p>

    <ul class="contacts">
      <li>
        <svg viewBox="0 0 16 16" aria-hidden="true"><path d="M3 1.5l3 .5 1 3.2-1.7 1.3a9 9 0 0 0 4.2 4.2L10.8 9l3.2 1 .5 3-1.8 1.7C7 14.5 1.5 9 1.3 3.3z" fill="var(--accent-blue)"/></svg>
        0472 915 348
      </li>
      <li>
        <svg viewBox="0 0 16 16" aria-hidden="true"><circle cx="8" cy="8" r="7" fill="var(--accent-blue)"/><path d="M1 8h14M8 1c3 3.5 3 10.5 0 14M8 1c-3 3.5-3 10.5 0 14" stroke="#000" stroke-width="1" fill="none"/></svg>
        www.tovrin.com.au
      </li>
      <li>
        <svg viewBox="0 0 16 16" aria-hidden="true"><rect x="1" y="3" width="14" height="10" rx="1" fill="var(--accent-blue)"/><path d="M1.5 3.5L8 9l6.5-5.5" stroke="#000" stroke-width="1.2" fill="none"/></svg>
        Warren.halbeck@tovrin.com.au
      </li>
    </ul>
  </section>

</main>
</body>
</html>
```